Cedar Brook Stables, LLC

Equestrian business card to promote equine retirement, farm sitting, short term board. Located in Aiken, SC.
Updates
Updated color schemes.
Contact Information for Business Card
Contact info, description of work.
Colors
0094D4
00A9DD
6FCCEA
C7EBF8
E9F6FB
59FF00
82FF00
B8FF75
E3FFCB
F4FFEA
F0912C
F2A743
F7CA91
FBE8D2
FDF5EE

```html
<!DOCTYPE html>
<html lang="en">
<head>
<meta charset="UTF-8">
<title>Cedar Brook Stables, LLC – Business Card</title>
<link href="https://fonts.googleapis.com/css2?family=Montserrat:wght@700&family=Poppins:wght@400;500&display=swap" rel="stylesheet">
<style>
  :root {
    --stage: #1f1f1f;
    --brand-blue: #0094D4;
    --brand-blue-mid: #00A9DD;
    --brand-blue-soft: #6FCCEA;
    --brand-blue-deep: #006a99;
    --meadow-lime: #82FF00;
    --meadow-lime-soft: #B8FF75;
    --harvest-orange: #F0912C;
    --harvest-orange-light: #F2A743;
    --paper: #ffffff;
    --ink: #2b2b2b;
    --ink-soft: #555555;
  }
  * { margin: 0; padding: 0; box-sizing: border-box; }
  html, body { width: 1200px; height: 1015px; overflow: hidden; }
  body {
    background: var(--stage);
    display: flex;
    flex-direction: column;
    align-items: center;
    justify-content: center;
    gap: 44px;
  }
  .card {
    position: relative;
    width: 760px;
    height: 434px;
    overflow: hidden;
    box-shadow: 0 14px 30px rgba(0,0,0,.55);
  }

  /* Front */
  .card-front {
    background: radial-gradient(circle at 45% 40%, var(--brand-blue-mid), var(--brand-blue) 70%);
    display: flex;
    align-items: center;
    justify-content: center;
    gap: 22px;
  }
  .front-mark {
    width: 64px; height: 64px; border-radius: 50%;
    background: var(--brand-blue-deep);
  }
  .front-name {
    font-family: "Montserrat", sans-serif;
    font-weight: 700;
    font-size: 40px;
    letter-spacing: 1px;
    color: var(--brand-blue-deep);
    text-transform: uppercase;
  }

  /* Back */
  .card-back { background: var(--paper); }
  .card-back svg.wave { position: absolute; inset: 0; }
  .brand {
    position: absolute;
    left: 44px; top: 140px;
  }
  .brand-line { display: flex; align-items: center; gap: 12px; }
  .brand-mark {
    width: 38px; height: 38px; border-radius: 50%;
    background: var(--harvest-orange);
  }
  .brand-name {
    font-family: "Montserrat", sans-serif;
    font-weight: 700;
    font-size: 21px;
    color: var(--ink);
    text-transform: uppercase;
  }
  .services {
    margin-top: 10px;
    padding-left: 50px;
    font-family: "Poppins", sans-serif;
    font-size: 13px;
    line-height: 1.5;
    color: var(--ink-soft);
  }
  .person {
    position: absolute;
    right: 44px; top: 38px;
    text-align: right;
  }
  .person-name {
    font-family: "Montserrat", sans-serif;
    font-weight: 700;
    font-size: 24px;
    color: var(--brand-blue);
    letter-spacing: .5px;
  }
  .person-title {
    font-family: "Poppins", sans-serif;
    font-size: 16px;
    color: var(--ink);
    margin-top: -2px;
  }
  .contact {
    position: absolute;
    right: 44px; bottom: 46px;
    list-style: none;
    font-family: "Poppins", sans-serif;
    font-size: 16px;
    color: var(--paper);
    text-align: right;
    line-height: 1.5;
  }
  .contact li { display: flex; justify-content: flex-end; align-items: flex-start; gap: 10px; }
  .contact svg { width: 16px; height: 16px; margin-top: 4px; flex: none; }
  .contact .address { line-height: 1.3; margin-top: 4px; }
</style>
</head>
<body>
  <section class="card card-front" aria-label="Card front">
    <span class="front-mark"></span>
    <span class="front-name">Cedar Brook Stables</span>
  </section>

  <section class="card card-back" aria-label="Card back">
    <svg class="wave" viewBox="0 0 760 434" preserveAspectRatio="none" aria-hidden="true">
      <path d="M0,346 C190,356 300,300 420,200 C520,118 610,96 700,92" fill="none" stroke="var(--meadow-lime)" stroke-width="9"/>
      <path d="M0,368 C200,378 310,320 430,222 C530,142 620,118 720,112" fill="none" stroke="var(--harvest-orange)" stroke-width="9"/>
      <path d="M0,386 C210,396 320,336 440,240 C540,160 630,136 760,128 L760,434 L0,434 Z" fill="var(--brand-blue)"/>
    </svg>

    <div class="brand">
      <div class="brand-line">
        <span class="brand-mark"></span>
        <span class="brand-name">Cedar Brook Stables</span>
      </div>
      <p class="services">Equine Retirement · Farm Sitting<br>Short-Term Board</p>
    </div>

    <div class="person">
      <p class="person-name">MARCUS HALE</p>
      <p class="person-title">Managing Director</p>
    </div>

    <ul class="contact">
      <li>803-555 014 227
        <svg viewBox="0 0 24 24"><path fill="var(--meadow-lime)" d="M6.6 10.8a15.1 15.1 0 0 0 6.6 6.6l2.2-2.2a1 1 0 0 1 1-.25 11.4 11.4 0 0 0 3.6.57 1 1 0 0 1 1 1V20a1 1 0 0 1-1 1A17 17 0 0 1 3 4a1 1 0 0 1 1-1h3.5a1 1 0 0 1 1 1c0 1.25.2 2.45.57 3.57a1 1 0 0 1-.25 1z"/></svg></li>
      <li>hello@cedarbrookstables.com
        <svg viewBox="0 0 24 24"><path fill="var(--meadow-lime)" d="M2 5h20v14H2z"/><path fill="none" stroke="var(--brand-blue)" stroke-width="1.8" d="M2 5l10 8 10-8"/></svg></li>
      <li>www.cedarbrookstables.com
        <svg viewBox="0 0 24 24"><circle cx="12" cy="12" r="9.5" fill="none" stroke="var(--meadow-lime)" stroke-width="2"/><path fill="none" stroke="var(--meadow-lime)" stroke-width="1.6" d="M2.5 12h19M12 2.5c3 3 3 16 0 19M12 2.5c-3 3-3 16 0 19"/></svg></li>
      <li class="address">118 Whiskey Road<br>Aiken, SC 29801
        <svg viewBox="0 0 24 24"><path fill="var(--meadow-lime)" d="M12 2a7 7 0 0 0-7 7c0 5 7 13 7 13s7-8 7-13a7 7 0 0 0-7-7zm0 9.5A2.5 2.5 0 1 1 12 6.5a2.5 2.5 0 0 1 0 5z"/></svg></li>
    </ul>
  </section>
</body>
</html>
```